KVOR Individual and Corporate Development Business Card Design

KVOR needs a business card design that is aligned with it's values and targetted markets. Coherent Lattice of Adaptive Reasoning Method's self diagnosis model and tools, which can be used for personal improvement and team/business performance enhancement, is based on the learnings of over 20 years of medical practitioning. KVOR supercharges personal effectiveness and awareness to also increase team and business performance.

The targetted markets are high performance individuals and teams who aspire seek to enhance their capabilities and achieve their absolute best potential.

Look and feel for the business card design we are looking for is high technology, premium, fresh, new and medical.

Target Market(s)

Industry/Entity Type

Business Consultant

Contact Information for Business Card

Logo, Full Name, Title, Phone number, Email, company name, Address,

Font styles to use
Sans Serif

Requirements
Must have
• Tag line: Maximising Performance for Highly Effective People
• Please use same colours as the logo.

```html
<!DOCTYPE html>
<html lang="en">
<head>
<meta charset="utf-8">
<title>KVOR Business Card</title>
<link href="https://fonts.googleapis.com/css2?family=Exo+2:wght@600;700;800&family=Open+Sans:wght@400;600&display=swap" rel="stylesheet">
<style>
  :root {
    --teal: #00a9c0;
    --teal-deep: #0096ad;
    --white: #ffffff;
    --paper: #f7f8f8;
    --ink: #2c2f33;
    --rule: #c9cdd0;
    --backdrop: #2a2c30;
  }
  * { box-sizing: border-box; margin: 0; padding: 0; }
  html, body { width: 1200px; height: 864px; overflow: hidden; }
  body {
    background: var(--backdrop);
    display: flex;
    flex-direction: column;
    align-items: center;
    justify-content: center;
    gap: 44px;
    font-family: "Open Sans", Arial, sans-serif;
  }
  .card {
    width: 620px;
    height: 354px;
    position: relative;
    overflow: hidden;
    border-radius: 3px;
  }

  /* Front */
  .card--front { background: var(--teal); }
  .front__brand {
    position: absolute;
    top: 46px; left: 0; right: 0;
    text-align: center;
    color: var(--white);
    font-family: "Exo 2", Arial, sans-serif;
  }
  .brand__name {
    font-weight: 800;
    font-size: 74px;
    line-height: 1;
    letter-spacing: 4px;
  }
  .brand__full {
    margin-top: 6px;
    font-weight: 700;
    font-size: 17px;
    line-height: 1.1;
    letter-spacing: 0.6px;
    text-transform: uppercase;
  }
  .front__band {
    position: absolute;
    left: 0; right: 0;
    top: 196px; height: 96px;
    background: var(--white);
    display: flex;
    align-items: center;
    justify-content: center;
  }
  .tagline {
    text-align: center;
    color: var(--teal);
    font-family: "Exo 2", Arial, sans-serif;
    font-weight: 700;
    font-size: 16px;
    line-height: 1.3;
    letter-spacing: 0.8px;
    text-transform: uppercase;
  }

  /* Back */
  .card--back { background: var(--paper); }
  .back__person {
    position: absolute;
    left: 48px; top: 128px;
  }
  .person__name {
    color: var(--teal);
    font-weight: 600;
    font-size: 23px;
    line-height: 1.1;
  }
  .person__title {
    color: var(--ink);
    font-size: 13px;
    margin-top: 2px;
  }
  .back__brand {
    position: absolute;
    right: 48px; top: 58px;
    text-align: left;
    color: var(--teal);
    font-family: "Exo 2", Arial, sans-serif;
    border-bottom: 1.5px solid var(--rule);
    padding: 0 0 6px 40px;
    display: flex;
    flex-direction: column;
  }
  .back__brand .brand__name { font-size: 60px; letter-spacing: 3px; }
  .back__brand .brand__full { font-size: 13.5px; margin-top: 4px; }
  .back__rule {
    position: absolute;
    left: 48px; right: 48px; top: 206px;
    border-top: 1px solid var(--rule);
  }
  .contacts {
    position: absolute;
    right: 48px; top: 220px;
    list-style: none;
    text-align: right;
  }
  .contact {
    display: flex;
    justify-content: flex-end;
    align-items: center;
    gap: 10px;
    color: var(--ink);
    font-size: 14.5px;
    line-height: 22px;
  }
  .contact svg { width: 13px; height: 13px; fill: var(--teal); flex: none; }
</style>
</head>
<body>

  <section class="card card--front" aria-label="Business card front">
    <div class="front__brand">
      <div class="brand__name">KVOR</div>
      <div class="brand__full">Coherent Lattice of<br>Adaptive Reasoning Method</div>
    </div>
    <div class="front__band">
      <p class="tagline">Maximising Performance for<br>Highly Effective People</p>
    </div>
  </section>

  <section class="card card--back" aria-label="Business card back">
    <div class="back__person">
      <div class="person__name">Daniel Mercer</div>
      <div class="person__title">Managing Director</div>
    </div>

    <div class="back__brand">
      <div class="brand__name">KVOR</div>
      <div class="brand__full">Coherent Lattice of<br>Adaptive Reasoning Method</div>
    </div>

    <div class="back__rule"></div>

    <ul class="contacts">
      <li class="contact">044-555-0182
        <svg viewBox="0 0 16 16" aria-hidden="true"><path d="M3.6 1.2l2.3 2.6-1.3 1.7c.9 2 2.6 3.8 4.8 4.9l1.7-1.3 2.6 2.3-1.4 2.5C6.9 13.6 2.3 9 1.2 3z"/></svg>
      </li>
      <li class="contact">123-555-0147
        <svg viewBox="0 0 16 16" aria-hidden="true"><path d="M4 1h6v4H4zM2 6h12v8H2zm2 2v2h2V8zm4 0v2h4V8zm-4 3v2h2v-2zm4 0v2h4v-2z"/></svg>
      </li>
      <li class="contact">123-555-0193
        <svg viewBox="0 0 16 16" aria-hidden="true"><path d="M4 0h8v16H4zm1.5 2v10h5V2zM8 13a.9.9 0 100 1.8A.9.9 0 008 13z"/></svg>
      </li>
      <li class="contact">hello@kvormail.com
        <svg viewBox="0 0 16 16" aria-hidden="true"><path d="M1 3h14v10H1zm1.5 1.5L8 9l5.5-4.5v-.1h-11z"/></svg>
      </li>
      <li class="contact">www.kvorlattice.com
        <svg viewBox="0 0 16 16" aria-hidden="true"><path d="M6.5 9.5l3-3 1 1-3 3zM9 3.5l1.5-1.5a3 3 0 014.2 4.2L13 7.8l-1-1 1.6-1.6a1.6 1.6 0 00-2.2-2.2L9.9 4.5zM7 12.5L5.5 14A3 3 0 011.3 9.8L3 8.2l1 1-1.6 1.6a1.6 1.6 0 002.2 2.2L6.1 11.5z"/></svg>
      </li>
    </ul>
  </section>

</body>
</html>
```